Floor Inspections and Consulting

We provide inspections and consulting services on various floor coverings, e.g. carpet, hardwood, etc. We also do expert witness work for attorneys due to floor covering failures. We current have a logo, just need it incorporated into a new design. I have examples of cards I have found on the internet that capture my attention and make a statement. I have included our original business card, which in my opinion is terrible, but it does have our logo on it.

```html
<!DOCTYPE html>
<html lang="en">
<head>
<meta charset="utf-8">
<title>Keystone Floor Inspections – Business Card</title>
<link rel="stylesheet" href="https://fonts.googleapis.com/css2?family=Russo+One&family=Arimo:wght@400;700&display=swap">
<style>
  :root {
    --stage: #3b3b3b;
    --card: #1f1f20;
    --card-edge: #2a2a2b;
    --orange: #e8730c;
    --white: #ffffff;
    --silver: #c9c9c9;
    --rule: #6a6a6a;
    --pattern-a: #232324;
    --pattern-b: #2b2b2c;
  }
  * { box-sizing: border-box; margin: 0; padding: 0; }
  html, body { width: 1200px; height: 1108px; overflow: hidden; }
  body {
    background: var(--stage);
    display: flex;
    align-items: center;
    justify-content: center;
    gap: 80px;
    font-family: "Arimo", Arial, sans-serif;
  }
  .card {
    position: relative;
    width: 420px;
    height: 720px;
    border-radius: 26px;
    background: var(--card);
    box-shadow: 0 18px 40px rgba(0,0,0,.45);
    overflow: hidden;
  }

  /* Front */
  .brand {
    position: absolute;
    top: 150px;
    left: 0; right: 0;
    display: flex;
    align-items: center;
    justify-content: center;
    gap: 14px;
  }
  .brand-square { width: 22px; height: 22px; background: var(--orange); }
  .brand-name {
    font-family: "Russo One", sans-serif;
    color: var(--orange);
    font-size: 27px;
    line-height: 1.15;
    letter-spacing: .5px;
    text-transform: uppercase;
  }
  .brand-rule {
    position: absolute;
    top: 262px;
    left: 70px; right: 70px;
    height: 2px;
    background: var(--orange);
  }
  .person-name {
    position: absolute;
    top: 388px;
    left: 0; right: 0;
    text-align: center;
    font-family: "Russo One", sans-serif;
    color: var(--orange);
    font-size: 28px;
    letter-spacing: .5px;
    text-transform: uppercase;
  }
  .contact-icons {
    position: absolute;
    top: 448px;
    left: 30px; right: 30px;
    display: flex;
    align-items: center;
    gap: 8px;
  }
  .contact-icons .line { flex: 1; height: 1px; background: var(--rule); }
  .icon {
    width: 36px; height: 36px;
    border-radius: 6px;
    background: var(--orange);
    display: flex; align-items: center; justify-content: center;
  }
  .contact-list {
    position: absolute;
    top: 510px;
    left: 0; right: 0;
    list-style: none;
    text-align: center;
    color: var(--white);
    font-size: 23px;
    line-height: 1.45;
  }
  .contact-list .accent { color: var(--orange); }

  /* Back */
  .pattern-field {
    position: absolute;
    inset: 0 0 240px 0;
    background: linear-gradient(160deg, var(--pattern-b) 0%, var(--pattern-a) 100%);
  }
  .back-brand {
    position: absolute;
    top: 538px;
    right: 60px;
    display: flex;
    align-items: center;
    gap: 10px;
  }
  .back-brand .brand-square { width: 18px; height: 18px; }
  .back-brand .brand-name { font-size: 26px; }
  .tagline {
    position: absolute;
    top: 608px;
    left: 40px; right: 40px;
    text-align: center;
    font-family: "Russo One", sans-serif;
    color: var(--silver);
    font-size: 24px;
    line-height: 1.3;
  }
</style>
</head>
<body>

  <article class="card card-front">
    <div class="brand">
      <span class="brand-square"></span>
      <span class="brand-name">Keystone Floor<br>Inspections</span>
    </div>
    <div class="brand-rule"></div>

    <h1 class="person-name">Daniel Marsh</h1>

    <div class="contact-icons">
      <span class="line"></span>
      <span class="icon" aria-label="Phone">
        <svg width="22" height="22" viewBox="0 0 24 24"><path fill="#1f1f20" d="M6.6 10.8a15.1 15.1 0 0 0 6.6 6.6l2.2-2.2c.3-.3.7-.4 1-.2 1.1.4 2.3.6 3.6.6.6 0 1 .4 1 1V20c0 .6-.4 1-1 1A17 17 0 0 1 3 4c0-.6.4-1 1-1h3.5c.6 0 1 .4 1 1 0 1.3.2 2.5.6 3.6.1.3 0 .7-.2 1z"/></svg>
      </span>
      <span class="icon" aria-label="Email">
        <svg width="22" height="22" viewBox="0 0 24 24"><rect x="3" y="5" width="18" height="14" rx="1.5" fill="#1f1f20"/><path d="M4 6.5l8 6 8-6" stroke="#e8730c" stroke-width="1.8" fill="none"/></svg>
      </span>
      <span class="icon" aria-label="Website">
        <svg width="22" height="22" viewBox="0 0 24 24"><circle cx="12" cy="12" r="9" fill="#1f1f20"/><path d="M3 12h18M12 3c3 3 3 15 0 18M12 3c-3 3-3 15 0 18" stroke="#e8730c" stroke-width="1.4" fill="none"/></svg>
      </span>
      <span class="line"></span>
    </div>

    <ul class="contact-list">
      <li>555-014-2270</li>
      <li>dan@keystonefloor.com</li>
      <li>www.<span class="accent">keystonefloor</span>.com</li>
    </ul>
  </article>

  <article class="card card-back">
    <div class="pattern-field" role="img" aria-label="Faint repeating brand pattern"></div>
    <div class="back-brand">
      <span class="brand-square"></span>
      <span class="brand-name">Keystone</span>
    </div>
    <p class="tagline">Certified Floor Covering<br>Inspection &amp; Consulting</p>
  </article>

</body>
</html>
```